Business Folder

I need a fresh, modern design for a business folder. I have our company's colors, logo, and a separate file for just the graphic part of our logo as a design element. No photo, just colors, gradients, and shadows to create depth. I like the idea of a rich grey as the background, however, I realize we'd have to lighten to 'Tax Advisory Services' part of our logo.

The design would just be the 'front' or outside of the folder from PressVale. Design file attached. You can find that here under 9 x 12 standard folder, Left and Right Pockets With Slit Both Sides:

https://www.pressvale-example.com/content.html?id=folderDownloadTemplates&rightMenuId=rightMenu&footerId=bodyFooterStyle6

```html
<!DOCTYPE html>
<html lang="en">
<head>
<meta charset="utf-8">
<title>Lumora Tax Advisory Folder</title>
<link href="https://fonts.googleapis.com/css2?family=Lato:wght@400&family=Montserrat:wght@700&display=swap" rel="stylesheet">
<style>
  :root {
    --backdrop: #3a393b;
    --paper: #ffffff;
    --navy: #0b5082;
    --band: #1b8fb8;
    --pocket: #4bc6e8;
    --photo-light: #e6ecf1;
    --photo-mid: #c3ced7;
    --photo-soft: #9aa8b5;
    --dieline: #111111;
  }
  html, body {
    margin: 0;
    padding: 0;
    width: 1200px;
    height: 1200px;
    overflow: hidden;
    background: var(--backdrop);
  }
  .folder-layout {
    display: block;
    width: 1200px;
    height: 1200px;
  }
  .brand-name {
    font-family: "Montserrat", sans-serif;
    font-weight: 700;
    font-size: 74px;
    letter-spacing: 2px;
    fill: var(--navy);
  }
  .address-label {
    font-family: "Lato", sans-serif;
    font-weight: 400;
    font-size: 16px;
    fill: var(--paper);
  }
  .address-line {
    font-family: "Lato", sans-serif;
    font-weight: 400;
    font-size: 12.5px;
    fill: var(--paper);
  }
</style>
</head>
<body>
<svg class="folder-layout" viewBox="0 0 1200 1200" xmlns="http://www.w3.org/2000/svg">
  <defs>
    <linearGradient id="photo-gradient" x1="0" y1="0" x2="0" y2="1">
      <stop offset="0" stop-color="var(--photo-mid)"/>
      <stop offset="0.5" stop-color="var(--photo-light)"/>
      <stop offset="1" stop-color="var(--photo-soft)"/>
    </linearGradient>
  </defs>

  <!-- side glue tabs -->
  <polygon class="tab-left" points="74,834 29,846 29,1054 74,1068" fill="none" stroke="var(--dieline)" stroke-width="2"/>
  <polygon class="tab-right" points="1127,834 1171,846 1171,1054 1127,1068" fill="none" stroke="var(--dieline)" stroke-width="2"/>

  <!-- cover sheet -->
  <rect class="cover" x="74" y="131" width="1053" height="703" fill="var(--paper)"/>

  <!-- front cover photo area -->
  <rect class="cover-photo" role="img" aria-label="Office desk photo with eyeglasses resting on printed charts beside a tablet and keyboard" x="600" y="392" width="527" height="442" fill="url(#photo-gradient)"/>

  <!-- back cover navy panel -->
  <path class="back-panel" d="M74,360 Q337,250 600,392 L600,834 L74,834 Z" fill="var(--navy)"/>

  <!-- plain curved band -->
  <path class="curve-band" d="M74,310 Q337,200 600,350 Q870,500 1127,420 L1127,500 Q870,580 600,392 Q337,250 74,360 Z" fill="var(--band)"/>

  <!-- brand name -->
  <text class="brand-name" x="1030" y="300" text-anchor="end">LUMORA</text>

  <!-- contact block -->
  <text class="address-label" x="336" y="751" text-anchor="middle">Address:</text>
  <text class="address-line" x="336" y="770" text-anchor="middle">Lorem ipsum dolor sit amet, consectetuer adipisc-</text>
  <text class="address-line" x="336" y="785" text-anchor="middle">ing elit, sed diam nonummy nibh</text>
  <text class="address-line" x="336" y="801" text-anchor="middle">Ph: 0000 000 000, Fax: 0000 000 000</text>

  <!-- pockets -->
  <polygon class="pocket-left" points="74,834 596,834 578,1068 74,1068" fill="var(--pocket)"/>
  <polygon class="pocket-right" points="604,834 1127,834 1127,1068 622,1068" fill="var(--pocket)"/>
</svg>
</body>
</html>
```